Executive & Leadership Coach needs a Graphic Design

We need a graphic design for a Leadership methodology/strategy that can be linked to The Harbor Prism

The Harbor Prism consists of:
1. Achievements
2. Personal Brand
3. Network
4. Executive Presence

This should Graphic Design will need to be used in PowerPoint presentations, training manuals and web pages

The design should be modern and provide the feeling of strength, trust, energy & creativity

Industry/Entity Type

Graphic Design

Font styles to use
Other font styles liked:
• Calibri, Verdana

```html
<!DOCTYPE html>
<html lang="en">
<head>
<meta charset="utf-8">
<title>The Harbor Prism — Leadership Gears</title>
<link href="https://fonts.googleapis.com/css2?family=Open+Sans:wght@400;700&display=swap" rel="stylesheet">
<style>
  :root {
    --bg: #ffffff;
    --ink: #333333;
    --gear-core: #f7941d;
    --gear-achievements: #27a9e1;
    --gear-presence: #8dc63f;
    --gear-network: #662d91;
    --gear-brand: #ec2a7b;
    --hub: #ffffff;
  }
  html, body {
    margin: 0;
    padding: 0;
    overflow: hidden;
    background: var(--bg);
  }
  .canvas {
    width: 1200px;
    height: 1000px;
    background: var(--bg);
    overflow: hidden;
  }
  .gear-diagram {
    display: block;
    width: 1200px;
    height: 1000px;
  }
  .gear-label {
    font-family: "Open Sans", Verdana, sans-serif;
    font-size: 23px;
    fill: var(--ink);
    text-anchor: middle;
  }
  .core-label {
    font-family: "Open Sans", Verdana, sans-serif;
    font-weight: 700;
    font-size: 40px;
    fill: var(--ink);
    text-anchor: middle;
  }
  .gear-achievements { fill: var(--gear-achievements); }
  .gear-presence { fill: var(--gear-presence); }
  .gear-network { fill: var(--gear-network); }
  .gear-brand { fill: var(--gear-brand); }
  .gear-core { fill: var(--gear-core); }
  .gear-hub { fill: var(--hub); stroke: #f2f2f2; stroke-width: 2; }
</style>
</head>
<body>
<main class="canvas">
  <svg class="gear-diagram" viewBox="213 140 822 740" xmlns="http://www.w3.org/2000/svg" role="img" aria-label="The Harbor Prism: Achievements, Executive Presence, Network and Personal Brand gears around a central Harbor Prism gear">
    <defs>
      <filter id="soft-shadow" x="-20%" y="-20%" width="140%" height="140%">
        <feDropShadow dx="2" dy="3" stdDeviation="3" flood-color="#000" flood-opacity="0.35"/>
      </filter>
      <filter id="hub-shadow" x="-20%" y="-20%" width="140%" height="140%">
        <feDropShadow dx="0" dy="0" stdDeviation="4" flood-color="#000" flood-opacity="0.4"/>
      </filter>
      <polygon id="tooth-small" points="-19,-95 -14,-124 14,-124 19,-95"/>
      <g id="gear-eight">
        <circle r="102"/>
        <use href="#tooth-small"/>
        <use href="#tooth-small" transform="rotate(45)"/>
        <use href="#tooth-small" transform="rotate(90)"/>
        <use href="#tooth-small" transform="rotate(135)"/>
        <use href="#tooth-small" transform="rotate(180)"/>
        <use href="#tooth-small" transform="rotate(225)"/>
        <use href="#tooth-small" transform="rotate(270)"/>
        <use href="#tooth-small" transform="rotate(315)"/>
      </g>
      <polygon id="tooth-large" points="-15,-96 -11,-120 11,-120 15,-96"/>
      <g id="gear-ten">
        <circle r="100"/>
        <use href="#tooth-large"/>
        <use href="#tooth-large" transform="rotate(36)"/>
        <use href="#tooth-large" transform="rotate(72)"/>
        <use href="#tooth-large" transform="rotate(108)"/>
        <use href="#tooth-large" transform="rotate(144)"/>
        <use href="#tooth-large" transform="rotate(180)"/>
        <use href="#tooth-large" transform="rotate(216)"/>
        <use href="#tooth-large" transform="rotate(252)"/>
        <use href="#tooth-large" transform="rotate(288)"/>
        <use href="#tooth-large" transform="rotate(324)"/>
      </g>
    </defs>

    <g class="gear gear-achievements" filter="url(#soft-shadow)" transform="translate(373 292) rotate(8)">
      <use href="#gear-eight"/>
    </g>
    <circle class="gear-hub" cx="373" cy="292" r="82" filter="url(#hub-shadow)"/>
    <text class="gear-label" x="373" y="299">Achievements</text>

    <g class="gear gear-presence" filter="url(#soft-shadow)" transform="translate(900 298) rotate(22)">
      <use href="#gear-eight"/>
    </g>
    <circle class="gear-hub" cx="900" cy="298" r="82" filter="url(#hub-shadow)"/>
    <text class="gear-label" x="896" y="294">Executive</text>
    <text class="gear-label" x="896" y="323">Presence</text>

    <g class="gear gear-network" filter="url(#soft-shadow)" transform="translate(440 677) rotate(14)">
      <use href="#gear-eight"/>
    </g>
    <circle class="gear-hub" cx="440" cy="677" r="82" filter="url(#hub-shadow)"/>
    <text class="gear-label" x="441" y="684">Network</text>

    <g class="gear gear-brand" filter="url(#soft-shadow)" transform="translate(828 677) rotate(0)">
      <use href="#gear-eight"/>
    </g>
    <circle class="gear-hub" cx="828" cy="677" r="82" filter="url(#hub-shadow)"/>
    <text class="gear-label" x="824" y="671">Personal</text>
    <text class="gear-label" x="824" y="700">Brand</text>

    <g class="gear gear-core" filter="url(#soft-shadow)" transform="translate(636 445) scale(1.58)">
      <use href="#gear-ten"/>
    </g>
    <circle class="gear-hub" cx="636" cy="445" r="125" filter="url(#hub-shadow)"/>
    <text class="core-label" x="631" y="440">Harbor</text>
    <text class="core-label" x="631" y="488">Prism</text>
  </svg>
</main>
</body>
</html>
```